Stationery Design Project for Nimbora, Chicago

Nimbora, a street parking application which helps car drivers find a street parking spot by offering an ideal path along which to look for parking. This path is calculated by our algorithm based on data (e.g. historical data, baseball games schedule, etc.). Along this path the driver will find a spot and will also save 70% of the search time. Customer we target is reg. between 21 and 45 yo.

We envision something young, fresh, bright and original. Slightly abstract maybe. It should represent the idea and elements of finding street parking in the city, e.g. car(s), parking spot, people, city, etc. (just ideas!).

Logo is attached.

Requirement:
- Business Cards (2 Sided Full Color CMYK)
- Letterhead (1 Sided Full Color CMYK)
- Envelope (1 Sided Full Color CMYK)
- Sticker (1 Sided Full Color CMYK), round with a 2inch diameter.

Reason: We're starting to get more and more designs and need more time to look into all of them. Very exciting!! Thanks to everybody!

Hi all, we're in the process of selecting our favs. Though choices!!! Really good submissions. Will keep you posted and sorry for the delay.

Target Market(s)

Car drivers and owners between 21 and 45

Industry/Entity Type

Parking

Requirements
Must have
• Sticker should be round and include company URL nimbora.com and the new logo which we will attach soon.
Should not have
• Should not be too serious or boring.

```html
<!DOCTYPE html>
<html lang="en">
<head>
<meta charset="utf-8">
<title>Nimbora Business Card</title>
<link rel="stylesheet" href="https://fonts.googleapis.com/css2?family=PT+Sans:wght@400;700&display=swap">
<style>
  :root {
    --page: #f1efec;
    --card-white: #ffffff;
    --ink-dark: #2f2f33;
    --name-blue: #5a58a2;
    --rule-grey: #6b6b75;
    --band-light: #3da6df;
    --band-dark: #2c3785;
    --back-light: #3d74c4;
    --back-dark: #284b9e;
    --mark-blue: #1f6fe0;
    --white: #ffffff;
  }
  * { margin: 0; padding: 0; box-sizing: border-box; }
  html, body { width: 1200px; height: 1111px; overflow: hidden; background: var(--page); }
  body { position: relative; font-family: "PT Sans", sans-serif; }

  .card { position: absolute; width: 680px; height: 388px; overflow: hidden; box-shadow: 0 4px 14px rgba(0,0,0,.18); }

  .card-front { left: 75px; top: 76px; background: var(--card-white); }
  .brand { position: absolute; left: 127px; top: 37px; display: flex; align-items: center; gap: 18px; }
  .brand-dot { width: 122px; height: 122px; border-radius: 50%; background: var(--mark-blue); }
  .brand-name { font-size: 82px; font-weight: 700; color: var(--ink-dark); letter-spacing: 1px; line-height: 1; }

  .holder { position: absolute; left: 0; right: 0; top: 196px; text-align: center; color: var(--name-blue); }
  .holder-name { font-size: 25px; font-weight: 700; }
  .holder-title { font-size: 19px; font-weight: 400; }

  .rule { position: absolute; left: 0; right: 0; top: 236px; height: 2px; background: var(--rule-grey); }

  .contact-band { position: absolute; left: 0; right: 0; top: 244px; bottom: 0;
    background: linear-gradient(90deg, var(--band-light) 0%, #3383c6 45%, var(--band-dark) 100%); color: var(--white); }
  .address { position: absolute; right: 329px; top: 48px; text-align: right; font-size: 17px; line-height: 23px; }
  .divider { position: absolute; left: 372px; top: 20px; width: 1px; height: 104px; background: rgba(255,255,255,.8); }
  .contact-list { position: absolute; left: 394px; top: 22px; list-style: none; font-size: 17px; line-height: 24.5px; }
  .contact-list li { display: flex; align-items: center; gap: 8px; }
  .contact-list svg { width: 12px; height: 12px; fill: var(--white); flex: none; }

  .card-back { left: 419px; top: 542px;
    background: radial-gradient(circle at 50% 50%, var(--back-light) 0%, var(--back-dark) 100%); }
  .back-mark { position: absolute; left: 182px; top: 25px; width: 336px; height: 336px; border-radius: 50%; background: var(--mark-blue); }
</style>
</head>
<body>
  <section class="card card-front">
    <div class="brand">
      <div class="brand-dot"></div>
      <span class="brand-name">nimbora</span>
    </div>
    <p class="holder"><span class="holder-name">Your Name ,</span> <span class="holder-title">Title</span></p>
    <div class="rule"></div>
    <div class="contact-band">
      <p class="address">Complex Name, Street Name<br>Area, City Name,000 000</p>
      <div class="divider"></div>
      <ul class="contact-list">
        <li><svg viewBox="0 0 12 12"><path d="M3 1l2 2-1 1.5c.7 1.4 1.8 2.5 3.2 3.2L8.7 6.7l2 2L9.5 10.5C5.3 10 2 6.7 1.5 2.5z"/></svg>+1 312 555 0148</li>
        <li><svg viewBox="0 0 12 12"><path d="M3.5 0h5a1 1 0 0 1 1 1v10a1 1 0 0 1-1 1h-5a1 1 0 0 1-1-1V1a1 1 0 0 1 1-1zm.5 2v6h4V2z"/></svg>+1 312 555 0192</li>
        <li><svg viewBox="0 0 12 12"><path d="M0 2.5h12v7H0zm1 1v.4l5 3 5-3v-.4z"/></svg>info@nimbora.com</li>
        <li><svg viewBox="0 0 12 12"><circle cx="6" cy="6" r="5.5"/></svg>www.nimbora.com</li>
      </ul>
    </div>
  </section>

  <section class="card card-back">
    <div class="back-mark"></div>
  </section>
</body>
</html>
```